Halvex Power

We need a business card for "Halvex power". I have uploaded the logo, the color of the card should be according to the logo "Blackish".
Basically halvex power is a solar company.
Also we would like a sample file in which we can edit the information such names and contact details ourselves
The card would be two sided with following details
1- logo on front and underneath the logo there should be a line saying
"Brighter . Smarter . Energy"
2-website i.e "www.halvexpowerco.com"
3- Icons for Facebook and Instagram that tells the clients we are available on both social sites.
4- name of the person with his/her designation underneath and email address
5-contact number
6- 1-800--- number with the extension number

its up to the designer how he/she places the details,but it must look professional

Industry/Entity Type

Business

Contact Information for Business Card

5-contact number

Requirements
Must have
• 1- logo on front and underneath the logo there should be a line saying
• "Brighter . Smarter . Energy"
• 2-website i.e "www.halvexpowerco.com"
• 3- Icons for Facebook and Instagram that tells the clients we are available on both social sites.
• 4- name of the person with his/her designation underneath and email address
• 5-contact number of the person
• 6- 1-800--- number with the extension number
• 7-card should be in black shade like the logo

```html
<!DOCTYPE html>
<html lang="en">
<head>
<meta charset="utf-8">
<title>Halvex Power — Business Card</title>
<link href="https://fonts.googleapis.com/css2?family=Roboto:wght@400;500;700&display=swap" rel="stylesheet">
<style>
  :root {
    --canvas-bg: #e9e7e3;
    --card-black: #1b1c1e;
    --card-green: #7ab537;
    --arc-grey: #8f8f8f;
    --arc-edge: #111111;
    --text-white: #ffffff;
    --tag-grey: #c9c9c9;
    --shadow: rgba(0,0,0,0.35);
  }
  * { margin: 0; padding: 0; box-sizing: border-box; }
  html, body { width: 1200px; height: 960px; overflow: hidden; }
  body {
    background: var(--canvas-bg);
    font-family: "Roboto", Arial, sans-serif;
    position: relative;
  }
  .card {
    position: absolute;
    width: 601px;
    height: 343px;
    overflow: hidden;
    box-shadow: 2px 3px 4px var(--shadow);
    background: var(--card-green);
  }
  .card-front { left: 314px; top: 113px; }
  .card-back  { left: 311px; top: 472px; }

  .front-sweep { position: absolute; inset: 0; width: 601px; height: 343px; }

  .social-marks { position: absolute; left: 20px; top: 24px; display: flex; gap: 6px; }
  .social-mark { width: 15px; height: 15px; background: var(--card-green); border-radius: 2px; }

  .brand { position: absolute; left: 40px; top: 128px; display: flex; align-items: center; gap: 12px; }
  .brand-dot { width: 18px; height: 18px; border-radius: 50%; background: var(--card-green); }
  .brand-name { font-size: 30px; font-weight: 700; color: var(--card-green); line-height: 1; letter-spacing: 0.2px; white-space: nowrap; }
  .brand-tagline { position: absolute; left: 70px; top: 164px; font-size: 13px; color: var(--tag-grey); letter-spacing: 0.3px; white-space: nowrap; }

  .person { position: absolute; right: 32px; top: 203px; text-align: right; color: var(--text-white); }
  .person-name { font-size: 18px; font-weight: 700; letter-spacing: 0.3px; }
  .person-title { font-size: 15px; font-weight: 400; margin-top: 2px; }

  .contacts { position: absolute; right: 32px; top: 259px; list-style: none; color: var(--text-white); font-size: 14.5px; }
  .contacts li { display: flex; justify-content: flex-end; align-items: center; gap: 6px; height: 20px; white-space: nowrap; }
  .contacts svg { width: 12px; height: 12px; fill: var(--text-white); }

  .back-brand { position: absolute; left: 0; right: 0; top: 145px; display: flex; justify-content: center; align-items: center; gap: 14px; }
  .back-brand .brand-dot { width: 22px; height: 22px; background: var(--text-white); }
  .back-brand .brand-name { font-size: 40px; color: var(--text-white); }
  .back-web { position: absolute; left: 0; right: 0; top: 297px; text-align: center; color: var(--text-white); font-size: 13px; letter-spacing: 4.2px; }
</style>
</head>
<body>

<section class="card card-front" aria-label="Business card front">
  <svg class="front-sweep" viewBox="0 0 601 343" aria-hidden="true">
    <path d="M0 0 H431 C500 15 500 110 432 200 C362 290 262 335 166 343 H0 Z" fill="var(--arc-grey)" stroke="var(--arc-edge)" stroke-width="2"/>
    <path d="M0 0 H431 C380 0 320 5 286 17 C425 22 480 85 430 175 C365 282 205 320 61 322 C78 334 95 340 110 343 H0 Z" fill="var(--card-black)"/>
  </svg>

  <div class="social-marks" aria-label="Social channels">
    <span class="social-mark"></span>
    <span class="social-mark"></span>
  </div>

  <div class="brand">
    <span class="brand-dot"></span>
    <span class="brand-name">Halvex Power</span>
  </div>
  <p class="brand-tagline">Brighter . Smarter . Energy</p>

  <div class="person">
    <p class="person-name">MARLA QUINT</p>
    <p class="person-title">PRESIDENT</p>
  </div>

  <ul class="contacts">
    <li>1-800-4179-3062
      <svg viewBox="0 0 12 12"><path d="M1 4 C1 2 3 1 6 1 C9 1 11 2 11 4 L9 5 L8 3.5 H4 L3 5 Z M2.5 6 H9.5 L10.5 11 H1.5 Z"/></svg>
    </li>
    <li>marla@halvexpowerco.com
      <svg viewBox="0 0 12 12"><path d="M0.5 2.5 H11.5 V3.2 L6 7 L0.5 3.2 Z M0.5 4.4 L6 8.2 L11.5 4.4 V9.5 H0.5 Z"/></svg>
    </li>
    <li>www.halvexpowerco.com
      <svg viewBox="0 0 12 12"><circle cx="6" cy="6" r="5.5"/><path d="M3 3 C4.5 4 4 6 5.5 6.5 C6.5 7 6 9 7 10 M8 2 C8.5 3.5 10 4 10.8 4.5" stroke="var(--card-green)" stroke-width="1" fill="none"/></svg>
    </li>
  </ul>
</section>

<section class="card card-back" aria-label="Business card back">
  <div class="back-brand">
    <span class="brand-dot"></span>
    <span class="brand-name">Halvex Power</span>
  </div>
  <p class="back-web">www.halvexpowerco.com</p>
</section>

</body>
</html>
```